SOLVE Study flyer

I need help designing a flyer for a research study that will include brain imaging in adolescents. The info is in the attached document. The study is called the Sequoia Outlook Lantern Valley Echo (SOLVE) study. Ideally this would be returned as a document that I can edit in the future as we will have several new recruitment phases (different age groups, etc. I also would love to have a logo designed as part of this project, but I recognize that might be a separate design request.

```html
<!DOCTYPE html>
<html lang="en">
<head>
<meta charset="utf-8">
<title>SOLVE Study Flyer</title>
<link rel="stylesheet" href="https://fonts.googleapis.com/css2?family=Anton&family=Outfit:wght@300;400;500;600&display=swap">
<style>
  :root {
    --cream: #fcf8ee;
    --ink: #1f1f1f;
    --blue: #0950a3;
    --gold: #fbb41d;
    --tape: #e0a14c;
  }
  * { box-sizing: border-box; margin: 0; padding: 0; }
  html, body { width: 882px; height: 1200px; overflow: hidden; background: var(--cream); }
  .flyer { position: relative; width: 882px; height: 1200px; background: var(--cream); font-family: "Outfit", sans-serif; color: var(--ink); }
  .abs { position: absolute; }
  .nowrap { white-space: nowrap; }

  .brand { left: 59px; top: 96px; display: flex; align-items: center; gap: 22px; }
  .brand-mark { width: 52px; height: 52px; background: var(--blue); }
  .brand-name { font-weight: 500; font-size: 30px; line-height: 1.1; color: var(--blue); }

  .hero-line { font-weight: 500; font-size: 42px; letter-spacing: -1px; line-height: 1; white-space: nowrap; }
  .hero-line.one { top: 214px; left: 66px; font-weight: 400; }
  .hero-line.two { top: 260px; left: 59px; }
  .hero-age { left: 58px; top: 312px; font-family: "Anton", sans-serif; font-size: 80px; line-height: 1; color: var(--ink); white-space: nowrap; }
  .hero-age span { color: var(--blue); }

  .intro { left: 59px; top: 420px; font-size: 21px; font-weight: 300; line-height: 27.6px; white-space: nowrap; }
  .intro b { font-weight: 500; }

  .divider { left: 53px; top: 587px; width: 264px; height: 3px; background: var(--gold); }

  .section-title { left: 56px; top: 616px; font-size: 27px; font-weight: 600; color: var(--blue); white-space: nowrap; }

  .steps { left: 56px; top: 666px; list-style: none; }
  .step { display: flex; gap: 24px; font-size: 19px; font-weight: 300; line-height: 25.8px; margin-bottom: 12.5px; white-space: nowrap; }
  .step b { font-weight: 500; }
  .step svg { flex: none; width: 36px; height: 36px; margin-top: 2px; }

  .comp { left: 59px; top: 1012px; font-size: 28px; font-weight: 500; line-height: 30px; }
  .comp-amount { left: 186px; top: 1054px; width: 178px; height: 92px; background: var(--gold); transform: rotate(-2.5deg); display: flex; align-items: center; justify-content: center; font-size: 56px; font-weight: 600; letter-spacing: -2px; }

  .photo { left: 470px; top: 62px; width: 384px; height: 404px; background: #fff; transform: rotate(-4deg); padding: 8px; box-shadow: 0 6px 16px rgba(0,0,0,0.12); }
  .photo-fill { width: 100%; height: 100%; background: linear-gradient(180deg, #7fae4a 0%, #9fbf6a 30%, #c9a58b 55%, #4f7fbf 80%, #d7dce6 100%); }

  .question { left: 483px; top: 468px; width: 298px; height: 214px; background: var(--blue); box-shadow: 0 10px 22px rgba(0,0,0,0.18); z-index: 2; }
  .question p { position: absolute; left: 39px; top: 36px; font-size: 30px; font-weight: 500; line-height: 35px; color: #fff; white-space: nowrap; }
  .tape { left: 566px; top: 458px; width: 110px; height: 28px; background: var(--tape); opacity: 0.85; transform: rotate(3deg); z-index: 3; }

  .eligibility { left: 469px; top: 674px; width: 358px; height: 476px; border: 1px solid var(--gold); }
  .elig-title { left: 500px; top: 727px; font-size: 30px; font-weight: 500; line-height: 38px; color: var(--blue); white-space: nowrap; }
  .criteria { left: 500px; top: 800px; list-style: none; }
  .criteria li { position: relative; padding-left: 31px; font-size: 19.5px; font-weight: 300; line-height: 26.5px; margin-bottom: 7.5px; white-space: nowrap; }
  .criteria svg { position: absolute; left: 0; top: 6px; width: 17px; height: 14px; }

  .contact { left: 500px; top: 1006px; font-size: 18px; font-weight: 400; line-height: 23.5px; white-space: nowrap; }
  .contact strong { color: var(--blue); font-weight: 600; }
  .email { left: 500px; top: 1094px; display: flex; align-items: center; gap: 12px; font-size: 20.5px; font-weight: 500; white-space: nowrap; }
  .email svg { width: 20px; height: 15px; }
</style>
</head>
<body>
<main class="flyer">
  <header class="brand abs">
    <span class="brand-mark"></span>
    <span class="brand-name">Allegheny Ridge<br>University</span>
  </header>

  <h1>
    <span class="hero-line one abs">Are you the</span>
    <span class="hero-line two abs">Parent of a Child</span>
    <span class="hero-age abs">Age <span>10-17?</span></span>
  </h1>

  <p class="intro abs"><b>Allegheny Ridge University researchers</b><br>are seeking girls <b>age 10-17</b> for a study<br>about brain activity in emotions and<br>decision making and how they relate<br>to puberty, anxiety and depression.</p>

  <div class="divider abs"></div>

  <h2 class="section-title abs">Study Participation Involves</h2>
  <ul class="steps abs">
    <li class="step">
      <svg viewBox="0 0 36 36" fill="var(--blue)"><circle cx="11" cy="16" r="7"/><path d="M3 34c0-6 4-9 8-9s8 3 8 9z"/><rect x="20" y="2" width="15" height="10" rx="1"/><path d="M23 12l-2 4 5-4z"/></svg>
      <span>One <b>one hour interview</b> (online<br>or in-person) where your child<br>will discuss their thoughts.</span>
    </li>
    <li class="step">
      <svg viewBox="0 0 36 36" fill="var(--blue)"><rect x="6" y="3" width="24" height="24" rx="2"/><rect x="10" y="8" width="16" height="2" fill="var(--cream)"/><rect x="10" y="13" width="16" height="2" fill="var(--cream)"/><rect x="10" y="18" width="16" height="2" fill="var(--cream)"/><rect x="2" y="28" width="32" height="4" rx="1"/></svg>
      <span>Online questionnaires<br>(parent and child).</span>
    </li>
    <li class="step">
      <svg viewBox="0 0 36 36" fill="var(--blue)"><circle cx="18" cy="14" r="12"/><circle cx="18" cy="14" r="6" fill="var(--cream)"/><rect x="4" y="28" width="28" height="3" rx="1"/><rect x="14" y="31" width="8" height="4"/></svg>
      <span>One <b>two hour visit</b> where your<br>child will complete an MRI scan,<br>answer questions about their<br>puberty stage, and have a small<br>hair sample taken to study<br>puberty hormones.</span>
    </li>
  </ul>

  <p class="comp abs">COMPENSATION<br>UP TO</p>
  <div class="comp-amount abs">$140</div>

  <div class="photo abs"><div class="photo-fill" role="img" aria-label="Photo of three smiling teenagers outdoors under green trees"></div></div>

  <div class="question abs"><p>Do they worry<br>or overthink<br>negative<br>emotions?</p></div>
  <div class="tape abs"></div>

  <div class="eligibility abs"></div>
  <h2 class="elig-title abs">Your child may be<br>eligible if they</h2>
  <ul class="criteria abs">
    <li><svg viewBox="0 0 17 14"><path d="M1 7l5 5L16 1" fill="none" stroke="var(--gold)" stroke-width="2.5"/></svg>Are age 10-17</li>
    <li><svg viewBox="0 0 17 14"><path d="M1 7l5 5L16 1" fill="none" stroke="var(--gold)" stroke-width="2.5"/></svg>Tend to worry or overthink<br>negative thoughts</li>
    <li><svg viewBox="0 0 17 14"><path d="M1 7l5 5L16 1" fill="none" stroke="var(--gold)" stroke-width="2.5"/></svg>Have not been diagnosed<br>with psychosis, learning<br>problems, or autism.</li>
  </ul>

  <p class="contact abs">Interested in participating?<br>Want more information?<br><strong>Please contact us!</strong></p>
  <p class="email abs">
    <svg viewBox="0 0 20 15"><rect width="20" height="15" rx="1" fill="var(--gold)"/><path d="M1 1l9 7 9-7" fill="none" stroke="#fff" stroke-width="1.5"/></svg>
    solvestudy@arhealth.edu
  </p>
</main>
</body>
</html>
```